Theme and starter template for small business powerpoint deck

We are starting a technology consulting company and would like to have a powerpoint/google slide theme and initial template. We are more concerned with the theme/colors at this point. Initial template can be pretty simple. We would want a cover slide, agenda slide, some content slides including text content, image content, a combination of both, etc. A closing slide. we have included jpg files of our logo, let us know if you would prefer eps/vector. I assume you may want exact color data as well?

Target Market(s)

Technology and Customer Experience Leadership at companies with 25 or more employees

Industry/Entity Type

Technology Consulting

Font styles to use
Sans Serif

Colors
0054AA
0677BA
7BADD7
CADEEF
E8F1F8

Requirements
Must have
• I have attached JPG and EPS and vector files to project. I would like to stay with those colors but open to slight variation if recommended.

```html
<!DOCTYPE html>
<html lang="en">
<head>
<meta charset="utf-8">
<title>Vantrel Slide Theme</title>
<link rel="stylesheet" href="https://fonts.googleapis.com/css2?family=Roboto:wght@400;500;700;900&display=swap">
<style>
:root{
  --stage:#2b2b2b;
  --ink:#111318;
  --text:#55585f;
  --navy:#0054AA;
  --blue:#0677BA;
  --sky:#7BADD7;
  --mist:#CADEEF;
  --ice:#E8F1F8;
  --white:#ffffff;
}
*{margin:0;padding:0;box-sizing:border-box}
html,body{width:1035px;height:1200px;overflow:hidden;background:var(--stage);font-family:'Roboto',Arial,sans-serif}
.stage{position:relative;width:1035px;height:1200px}
.slide{position:absolute;width:449px;height:252px;background:var(--white);overflow:hidden}
.abs{position:absolute}
.brand{position:absolute;display:flex;align-items:center;gap:3px;font-family:'Roboto',Arial,sans-serif;font-weight:700;color:var(--ink);letter-spacing:1.2px;line-height:1}
.brand-dot{width:5px;height:5px;background:var(--navy)}
.slide-title{position:absolute;left:25px;top:14px;font-size:13.5px;font-weight:500;letter-spacing:.8px;color:var(--ink)}
.head-brand{right:26px;top:14px;font-size:12.5px}
.foot-line{position:absolute;left:0;top:235px;width:336px;height:2px;background:var(--mist)}
.foot-band{position:absolute;left:0;top:238px;width:404px;height:14px;background:var(--blue);clip-path:polygon(0 0,100% 0,96% 100%,0 100%)}
.foot-copy{position:absolute;left:25px;top:242px;font-size:5.4px;color:var(--white)}
.foot-page{position:absolute;right:0;top:233px;width:48px;height:19px;background:var(--navy);clip-path:polygon(14% 0,100% 0,100% 100%,0 100%);font-size:5.4px;color:var(--white);padding:6px 0 0 12px}
.photo{position:absolute}
.body{font-size:5.1px;line-height:1.9;color:var(--text)}
.sub{font-size:9px;font-weight:500;color:var(--ink);line-height:1.35}

/* cover */
.cover-date{left:25px;top:84px;font-size:6.6px;font-weight:500;color:var(--navy)}
.cover-title{left:24px;top:94px;font-size:28px;font-weight:700;letter-spacing:.6px;color:var(--ink)}
.cover-lede{left:25px;top:133px;width:170px;font-size:6.4px;line-height:1.8;color:var(--ink);font-weight:500}
.cover-copy{left:25px;top:212px;font-size:6.4px;color:#666}
.cover-art{position:absolute;left:0;top:0;width:449px;height:252px}

/* agenda */
.agenda-item{position:absolute;left:210px;width:214px;height:22px}
.agenda-num{position:absolute;left:0;top:1px;width:19px;height:20px;background:var(--blue);clip-path:polygon(25% 0,75% 0,100% 50%,75% 100%,25% 100%,0 50%);color:var(--white);font-size:6px;font-weight:500;display:flex;align-items:center;justify-content:center}
.agenda-bar{position:absolute;left:25px;top:0;width:189px;height:22px;background:var(--white);box-shadow:0 1px 3px rgba(0,0,0,.18);clip-path:polygon(5% 0,100% 0,100% 100%,5% 100%,0 50%);border-right:2px solid var(--blue);font-size:8.6px;font-weight:500;color:var(--ink);padding:6px 0 0 18px}
.agenda-item.first .agenda-num{background:var(--navy)}
.agenda-item.first .agenda-bar{border-right-color:var(--navy)}

/* intro */
.intro-row{position:absolute;left:25px;width:400px;display:flex;gap:16px;align-items:center}
.intro-mark{width:7px;height:7px;flex:none;background:var(--blue)}
.intro-row p{font-size:5.3px;line-height:1.75;color:var(--text)}

/* about */
.about-col{position:absolute;top:44px;width:187px}
.about-col .sub{margin-bottom:9px}
.about-col .body p{margin-bottom:6px}

/* values */
.values-callout{position:absolute;left:197px;top:162px;width:200px;height:54px}
.callout-back{position:absolute;left:0;top:4px;width:190px;height:50px;background:var(--navy);clip-path:polygon(6% 0,100% 0,94% 100%,0 100%)}
.callout-front{position:absolute;left:4px;top:0;width:196px;height:50px;background:var(--blue);clip-path:polygon(6% 0,100% 0,94% 100%,0 100%);padding:9px 0 0 27px;color:var(--white)}
.callout-front h4{font-size:8.6px;font-weight:500;margin-bottom:6px}
.callout-front p{font-size:5.1px;line-height:1.4;width:150px}

/* strategy */
.strat-grid{position:absolute;left:29px;top:56px;width:391px;height:147px;display:grid;grid-template-columns:repeat(3,1fr);grid-template-rows:repeat(2,1fr);box-shadow:0 1px 5px rgba(0,0,0,.12)}
.strat-cell{text-align:center;padding:12px 9px 0;background:var(--white)}
.strat-cell h4{font-size:7.8px;font-weight:500;color:var(--ink);margin-bottom:5px}
.strat-cell p{font-size:5.2px;line-height:1.6;color:var(--text)}
.strat-cell.blue{background:var(--blue)}
.strat-cell.navy{background:var(--navy)}
.strat-cell.sky{background:var(--sky)}
.strat-cell.blue h4,.strat-cell.navy h4,.strat-cell.sky h4,
.strat-cell.blue p,.strat-cell.navy p,.strat-cell.sky p{color:var(--white)}

/* services */
.svc-card{position:absolute;top:49px;width:125px;height:162px;background:var(--white);box-shadow:0 1px 6px rgba(0,0,0,.1)}
.svc-frame{position:absolute;left:0;top:0;width:125px;height:62px}
.svc-photo{position:absolute;left:7px;top:6px;width:111px;height:74px}
.svc-card h4{position:absolute;left:13px;top:92px;font-size:7.8px;font-weight:500;color:var(--ink)}
.svc-list{position:absolute;left:13px;top:108px;list-style:none}
.svc-list li{display:flex;align-items:center;gap:4px;font-size:5.4px;color:var(--text);height:11px}
.tick{width:5px;height:5px;flex:none}

/* contact */
.contact-bg{position:absolute;inset:0;background:linear-gradient(110deg,#0b1320 0%,#0f1d33 42%,#14385f 66%,#0677BA 88%,#7BADD7 100%)}
.contact-brand{left:52px;top:36px;font-size:18px;color:var(--white)}
.contact-title{left:52px;top:78px;font-size:13px;font-weight:500;color:var(--white)}
.contact-addr{left:52px;top:100px;font-size:6.5px;line-height:1.6;color:var(--white);font-weight:500}
.contact-line{position:absolute;left:52px;display:flex;align-items:center;gap:5px;font-size:6.8px;color:var(--white);font-weight:500}
.contact-line svg{width:8px;height:8px}
</style>
</head>
<body>
<div class="stage">

  <!-- Cover -->
  <section class="slide" style="left:46px;top:35px">
    <svg class="cover-art" viewBox="0 0 449 252" role="img" aria-label="Three triangular photo panels of consultants at work, tinted in brand blues">
      <polygon points="304,1 378,126 230,126" fill="#0677BA"/>
      <polygon points="230,128 304,252 157,252" fill="#7BADD7"/>
      <polygon points="378,128 449,252 304,252" fill="#0054AA"/>
    </svg>
    <div class="brand" style="left:25px;top:19px;font-size:14px"><span>VANTREL</span><span class="brand-dot"></span></div>
    <div class="abs cover-date">27 July 2024</div>
    <h1 class="abs cover-title">VANTREL</h1>
    <p class="abs cover-lede">Lorem ipsum dolor sit amet, consectetur adipiscing incididunt ut labore et dolore magna aliqua.</p>
    <div class="abs cover-copy">© 2024 Vantrel. All Rights Reserved</div>
  </section>

  <!-- Agenda -->
  <section class="slide" style="left:524px;top:35px">
    <div class="photo" role="img" aria-label="Photo of two engineers reviewing a laptop in a server room" style="left:0;top:0;width:181px;height:252px;background:linear-gradient(160deg,#0b2a4f 0%,#0677BA 50%,#0a2240 100%)"></div>
    <div class="abs" style="left:210px;top:14px;font-size:12px;font-weight:500;letter-spacing:.6px;color:var(--ink)">AGENDA SLIDE</div>
    <div class="brand" style="right:25px;top:17px;font-size:8.5px"><span>VANTREL</span><span class="brand-dot" style="width:4px;height:4px"></span></div>
    <div class="agenda-item first" style="top:47px"><div class="agenda-num">01</div><div class="agenda-bar">Introduction</div></div>
    <div class="agenda-item" style="top:80px"><div class="agenda-num">02</div><div class="agenda-bar">Our Services</div></div>
    <div class="agenda-item" style="top:113px"><div class="agenda-num">03</div><div class="agenda-bar">Our Values</div></div>
    <div class="agenda-item" style="top:145px"><div class="agenda-num">04</div><div class="agenda-bar">Quotes</div></div>
    <div class="agenda-item" style="top:178px"><div class="agenda-num">05</div><div class="agenda-bar">Our Team</div></div>
    <div class="agenda-item" style="top:211px"><div class="agenda-num">06</div><div class="agenda-bar">Contact Us</div></div>
  </section>

  <!-- Introduction -->
  <section class="slide" style="left:46px;top:329px">
    <h2 class="slide-title">INTRODUCTION</h2>
    <div class="brand head-brand"><span>VANTREL</span><span class="brand-dot"></span></div>
    <div class="intro-row" style="top:54px"><span class="intro-mark"></span><p>Lorem ipsum dolor sit amet, consectetur adipiscing elit, sed do eiusmod tempor incididunt ut labore et dolore magna aliqua. Quis ipsum suspendisse ultrices gravida. Risus commodo viverra maecenas accumsan lacus vel facilisis.</p></div>
    <div class="intro-row" style="top:79px"><span class="intro-mark"></span><p>Sed ut perspiciatis unde omnis iste natus error sit voluptatem accusantium doloremque laudantium, totam rem aperiam, eaque ipsa quae ab illo inventore veritatis et quasi architecto beatae vitae dicta sunt explicabo.</p></div>
    <div class="intro-row" style="top:104px"><span class="intro-mark"></span><p>Lorem ipsum dolor sit amet, consectetur adipiscing elit, sed do eiusmod tempor incididunt ut labore et dolore magna aliqua. Quis ipsum suspendisse ultrices gravida. Risus commodo viverra maecenas accumsan lacus vel facilisis.</p></div>
    <div class="intro-row" style="top:129px"><span class="intro-mark"></span><p>Sed ut perspiciatis unde omnis iste natus error sit voluptatem accusantium doloremque laudantium, totam rem aperiam, eaque ipsa quae ab illo inventore veritatis et quasi architecto beatae vitae dicta sunt explicabo.</p></div>
    <div class="intro-row" style="top:154px"><span class="intro-mark"></span><p>Lorem ipsum dolor sit amet, consectetur adipiscing elit, sed do eiusmod tempor incididunt ut labore et dolore magna aliqua. Quis ipsum suspendisse ultrices gravida. Risus commodo viverra maecenas accumsan lacus vel facilisis.</p></div>
    <div class="intro-row" style="top:179px"><span class="intro-mark"></span><p>Sed ut perspiciatis unde omnis iste natus error sit voluptatem accusantium doloremque laudantium, totam rem aperiam, eaque ipsa quae ab illo inventore veritatis et quasi architecto beatae vitae dicta sunt explicabo.</p></div>
    <div class="foot-line"></div><div class="foot-band"></div>
    <div class="foot-copy">Copyright © 2024 Vantrel. All rights reserved.</div>
    <div class="foot-page">Page 03</div>
  </section>

  <!-- About us -->
  <section class="slide" style="left:524px;top:329px">
    <h2 class="slide-title">ABOUT US</h2>
    <div class="brand head-brand"><span>VANTREL</span><span class="brand-dot"></span></div>
    <div class="about-col" style="left:25px">
      <h3 class="sub">Lorem ipsum dolor sit amet, consectetur adipiscing elit, sed do eiusmod</h3>
      <div class="body">
        <p>Sed ut perspiciatis unde omnis iste natus error sit voluptatem accusantium doloremque laudantium, totam rem aperiam, eaque ipsa quae ab veritatis et quasi architecto beatae vitae dicta sunt explicabo.</p>
        <p>Nemo enim ipsam voluptatem quia voluptas sit aspernatur aut odit aut fugit, sed quia consequuntur magni dolores eos qui ratione voluptatem sequi nesciunt. Neque porro quisquam est, qui dolorem ipsum quia dolor sit amet, consectetur, adipisci velit, sed quia non numquam eius modi tempora incidunt ut labore et dolore magnam aliquam quaerat voluptatem. Ut enim ad minima veniam, quis nostrum exercitationem ullam corporis suscipit laboriosam,</p>
        <p>Sed ut perspiciatis unde omnis iste natus error sit voluptatem accusantium doloremque laudantium, totam rem aperiam, eaque ipsa quae ab veritatis et quasi architecto beatae vitae dicta sunt explicabo.</p>
      </div>
    </div>
    <div class="about-col" style="left:236px">
      <h3 class="sub">Lorem ipsum dolor sit amet, consectetur adipiscing elit, sed do eiusmod</h3>
      <div class="body">
        <p>Sed ut perspiciatis unde omnis iste natus error sit voluptatem accusantium doloremque laudantium, totam rem aperiam, eaque ipsa quae ab veritatis et quasi architecto beatae vitae dicta sunt explicabo.</p>
        <p>Nemo enim ipsam voluptatem quia voluptas sit aspernatur aut odit aut fugit, sed quia consequuntur magni dolores eos qui ratione voluptatem sequi nesciunt. Neque porro quisquam est, qui dolorem ipsum quia dolor sit amet, consectetur, adipisci velit, sed quia non numquam eius modi tempora incidunt ut labore et dolore magnam aliquam quaerat voluptatem. Ut enim ad minima veniam, quis nostrum exercitationem ullam corporis suscipit laboriosam,</p>
        <p>Sed ut perspiciatis unde omnis iste natus error sit voluptatem accusantium doloremque laudantium, totam rem aperiam, eaque ipsa quae ab veritatis et quasi architecto beatae vitae dicta sunt explicabo.</p>
      </div>
    </div>
    <div class="foot-line"></div><div class="foot-band"></div>
    <div class="foot-copy">Copyright © 2024 Vantrel. All rights reserved.</div>
    <div class="foot-page">Page 04</div>
  </section>

  <!-- Our values -->
  <section class="slide" style="left:46px;top:619px">
    <h2 class="slide-title">OUR VALUES</h2>
    <div class="brand head-brand"><span>VANTREL</span><span class="brand-dot"></span></div>
    <h3 class="sub abs" style="left:25px;top:50px;width:185px">Lorem ipsum dolor sit amet, consectetur adipiscing elit, sed do eiusmod</h3>
    <div class="body abs" style="left:25px;top:83px;width:178px">
      <p style="margin-bottom:5px">Sed ut perspiciatis unde omnis iste natus error sit voluptatem accusantium doloremque laudantium, totam rem aperiam, eaque ipsa quae ab illo inventore veritatis et quasi architecto beatae vitae dicta sunt explicabo.</p>
      <p>Nemo enim ipsam voluptatem quia voluptas sit aspernatur aut odit aut fugit, sed quia consequuntur magni dolores eos qui ratione voluptatem sequi nesciunt. Neque porro quisquam est, qui dolorem ipsum quia dolor sit amet, consectetur, adipisci velit, sed quia non numquam eius modi tempora incidunt ut labore et dolore magnam aliquam quaerat voluptatem. Ut enim ad minima veniam, quis nostrum exercitationem ullam corporis suscipit laboriosam,</p>
    </div>
    <div class="photo" role="img" aria-label="Photo of three colleagues discussing work around an office table" style="left:218px;top:38px;width:205px;height:186px;clip-path:polygon(22% 0,100% 0,100% 100%,0 100%);background:linear-gradient(150deg,#E8F1F8 0%,#7BADD7 50%,#1d3f66 100%)"></div>
    <div class="values-callout">
      <div class="callout-back"></div>
      <div class="callout-front">
        <h4>Lorem ipsum dolor sit amet,</h4>
        <p>Sed ut perspiciatis unde omnis natus error sit voluptatem accusantium doloremque laudantium,</p>
      </div>
    </div>
    <div class="foot-line"></div><div class="foot-band"></div>
    <div class="foot-copy">Copyright © 2024 Vantrel. All rights reserved.</div>
    <div class="foot-page">Page 05</div>
  </section>

  <!-- Our strategy -->
  <section class="slide" style="left:524px;top:619px">
    <h2 class="slide-title">OUR STRATEGY</h2>
    <div class="brand head-brand"><span>VANTREL</span><span class="brand-dot"></span></div>
    <div class="strat-grid">
      <div class="strat-cell blue"><h4>Lorem ipsum dolor sit</h4><p>Lorem ipsum dolor sit amet, consectetur adipiscing elit, sed do eiusmod tempor incididunt ut labore et dolore magna suspendisse ultrices aliqua.</p></div>
      <div class="strat-cell"><h4>Lorem ipsum dolor sit</h4><p>Lorem ipsum dolor sit amet, consectetur adipiscing elit, sed do eiusmod tempor incididunt ut labore et dolore magna suspendisse ultrices aliqua.</p></div>
      <div class="strat-cell navy"><h4>Lorem ipsum dolor sit</h4><p>Lorem ipsum dolor sit amet, consectetur adipiscing elit, sed do eiusmod tempor incididunt ut labore et dolore magna suspendisse ultrices aliqua.</p></div>
      <div class="strat-cell"><h4>Lorem ipsum dolor sit</h4><p>Lorem ipsum dolor sit amet, consectetur adipiscing elit, sed do eiusmod tempor incididunt ut labore et dolore magna suspendisse ultrices aliqua.</p></div>
      <div class="strat-cell sky"><h4>Lorem ipsum dolor sit</h4><p>Lorem ipsum dolor sit amet, consectetur adipiscing elit, sed do eiusmod tempor incididunt ut labore et dolore magna suspendisse ultrices aliqua.</p></div>
      <div class="strat-cell"><h4>Lorem ipsum dolor sit</h4><p>Lorem ipsum dolor sit amet, consectetur adipiscing elit, sed do eiusmod tempor incididunt ut labore et dolore magna suspendisse ultrices aliqua.</p></div>
    </div>
    <div class="foot-line"></div><div class="foot-band"></div>
    <div class="foot-copy">Copyright © 2024 Vantrel. All rights reserved.</div>
    <div class="foot-page">Page 06</div>
  </section>

  <!-- Our services -->
  <section class="slide" style="left:41px;top:909px">
    <h2 class="slide-title">OUR SERVICES</h2>
    <div class="brand head-brand"><span>VANTREL</span><span class="brand-dot"></span></div>

    <article class="svc-card" style="left:25px">
      <div class="svc-frame" style="background:var(--navy)"></div>
      <div class="svc-photo" role="img" aria-label="Photo of a team reviewing data on monitors in a control room" style="background:linear-gradient(150deg,#0d2746,#0677BA 55%,#0b1f38)"></div>
      <h4>Lorem ipsum dolor amet</h4>
      <ul class="svc-list">
        <li><svg class="tick" viewBox="0 0 10 10"><circle cx="5" cy="5" r="5" fill="#0054AA"/><path d="M2.8 5.2l1.6 1.6 3-3.2" stroke="#fff" stroke-width="1.4" fill="none"/></svg>Sed perspiciatis unde omnis iste</li>
        <li><svg class="tick" viewBox="0 0 10 10"><circle cx="5" cy="5" r="5" fill="#0054AA"/><path d="M2.8 5.2l1.6 1.6 3-3.2" stroke="#fff" stroke-width="1.4" fill="none"/></svg>Sed perspiciatis unde iste</li>
        <li><svg class="tick" viewBox="0 0 10 10"><circle cx="5" cy="5" r="5" fill="#0054AA"/><path d="M2.8 5.2l1.6 1.6 3-3.2" stroke="#fff" stroke-width="1.4" fill="none"/></svg>Sed perspiciatis unde omnis iste</li>
        <li><svg class="tick" viewBox="0 0 10 10"><circle cx="5" cy="5" r="5" fill="#0054AA"/><path d="M2.8 5.2l1.6 1.6 3-3.2" stroke="#fff" stroke-width="1.4" fill="none"/></svg>Sed perspiciatis unde iste</li>
      </ul>
    </article>

    <article class="svc-card" style="left:162px">
      <div class="svc-frame" style="background:var(--sky)"></div>
      <div class="svc-photo" role="img" aria-label="Photo of engineers working together at desks in a tech office" style="background:linear-gradient(150deg,#12335a,#3f86bf 55%,#0f2542)"></div>
      <h4>Lorem ipsum dolor amet</h4>
      <ul class="svc-list">
        <li><svg class="tick" viewBox="0 0 10 10"><circle cx="5" cy="5" r="5" fill="#0054AA"/><path d="M2.8 5.2l1.6 1.6 3-3.2" stroke="#fff" stroke-width="1.4" fill="none"/></svg>Sed perspiciatis unde omnis iste</li>
        <li><svg class="tick" viewBox="0 0 10 10"><circle cx="5" cy="5" r="5" fill="#0054AA"/><path d="M2.8 5.2l1.6 1.6 3-3.2" stroke="#fff" stroke-width="1.4" fill="none"/></svg>Sed perspiciatis unde iste</li>
        <li><svg class="tick" viewBox="0 0 10 10"><circle cx="5" cy="5" r="5" fill="#0054AA"/><path d="M2.8 5.2l1.6 1.6 3-3.2" stroke="#fff" stroke-width="1.4" fill="none"/></svg>Sed perspiciatis unde omnis iste</li>
        <li><svg class="tick" viewBox="0 0 10 10"><circle cx="5" cy="5" r="5" fill="#0054AA"/><path d="M2.8 5.2l1.6 1.6 3-3.2" stroke="#fff" stroke-width="1.4" fill="none"/></svg>Sed perspiciatis unde iste</li>
      </ul>
    </article>

    <article class="svc-card" style="left:299px">
      <div class="svc-frame" style="background:var(--blue)"></div>
      <div class="svc-photo" role="img" aria-label="Photo of two colleagues looking at a computer screen" style="background:linear-gradient(150deg,#E8F1F8,#7BADD7 55%,#2b5680)"></div>
      <h4>Lorem ipsum dolor amet</h4>
      <ul class="svc-list">
        <li><svg class="tick" viewBox="0 0 10 10"><circle cx="5" cy="5" r="5" fill="#0054AA"/><path d="M2.8 5.2l1.6 1.6 3-3.2" stroke="#fff" stroke-width="1.4" fill="none"/></svg>Sed perspiciatis unde omnis iste</li>
        <li><svg class="tick" viewBox="0 0 10 10"><circle cx="5" cy="5" r="5" fill="#0054AA"/><path d="M2.8 5.2l1.6 1.6 3-3.2" stroke="#fff" stroke-width="1.4" fill="none"/></svg>Sed perspiciatis unde iste</li>
        <li><svg class="tick" viewBox="0 0 10 10"><circle cx="5" cy="5" r="5" fill="#0054AA"/><path d="M2.8 5.2l1.6 1.6 3-3.2" stroke="#fff" stroke-width="1.4" fill="none"/></svg>Sed perspiciatis unde omnis iste</li>
        <li><svg class="tick" viewBox="0 0 10 10"><circle cx="5" cy="5" r="5" fill="#0054AA"/><path d="M2.8 5.2l1.6 1.6 3-3.2" stroke="#fff" stroke-width="1.4" fill="none"/></svg>Sed perspiciatis unde iste</li>
      </ul>
    </article>

    <div class="foot-line"></div><div class="foot-band"></div>
    <div class="foot-copy">Copyright © 2024 Vantrel. All rights reserved.</div>
    <div class="foot-page">Page 07</div>
  </section>

  <!-- Contact -->
  <section class="slide" style="left:525px;top:910px">
    <div class="contact-bg" role="img" aria-label="Photo of glass office towers in a city at dusk"></div>
    <div class="brand contact-brand"><span>VANTREL</span><span class="brand-dot" style="width:6px;height:6px;background:var(--sky)"></span></div>
    <h2 class="abs contact-title">Contact Us</h2>
    <p class="abs contact-addr">Level 4, 210 Marlow Ave, Eastbridge,<br>NY 10000, USA</p>
    <div class="contact-line" style="top:137px">
      <svg viewBox="0 0 10 10"><path d="M2.2 1l1.6 2-.9 1.1c.6 1.3 1.6 2.3 2.9 2.9l1.1-.9 2 1.6-.8 1.5C4.8 9 1 5.2 .8 1.9z" fill="#7BADD7"/></svg>555-0142-7788
    </div>
    <div class="contact-line" style="top:154px">
      <svg viewBox="0 0 10 10"><rect x=".5" y="2" width="9" height="6.5" fill="#7BADD7"/><path d="M.5 2l4.5 3.6L9.5 2" stroke="#0b1320" stroke-width=".8" fill="none"/></svg>info@vantrel.com
    </div>
    <div class="contact-line" style="top:171px">
      <svg viewBox="0 0 10 10"><circle cx="5" cy="5" r="4.3" fill="none" stroke="#7BADD7" stroke-width=".9"/><path d="M.7 5h8.6M5 .7c-2.4 2.6-2.4 6 0 8.6M5 .7c2.4 2.6 2.4 6 0 8.6" stroke="#7BADD7" stroke-width=".8" fill="none"/></svg>www.vantrel.com
    </div>
  </section>

</div>
</body>
</html>
```